Refresh of far from plain IT company website

Our web site is starting to show it's age. You can see the existing site here: www.plumbwick.net. As a growing company we want to come across as a dynamic collection of IT experts.

We want to update the design so are open to any colour palette and look, but want to retain our current table logo. We use the logo on our business cards but with a white background - see the attached file, so you don't need to keep the brown or the green.

The design should consider the range of browsers that will be looking at the site - so please show how it will look on a wide screen laptop and a 768x1024 tablet.

We want to add some pages about our team and their skills, probably with photos of each person on the team.

This is an uncoded project - the PSD files of the design is required, not coding.
Updates

Thanks everyone for the submissions so far.  It's a holiday day in the UK today but we will get some feedback on the designs so far out to you.

Target Market(s)

Architects and other creative types looking for IT support

Industry/Entity Type

Business

Font styles to use
Serif
Sans Serif

Requirements
Must have
• Must look good on a laptop and an iPad.

```html
<!DOCTYPE html>
<html lang="en">
<head>
<meta charset="utf-8">
<title>Plumbwick – IT Support</title>
<link href="https://fonts.googleapis.com/css2?family=Oxygen:wght@400;700&family=Arimo:wght@400&display=swap" rel="stylesheet">
<style>
:root{
  --plum:#8e0a4e;
  --plum-dark:#7a0842;
  --gold:#d9ac00;
  --gold-light:#e6bd10;
  --ink:#222;
  --text:#333;
  --muted:#666;
  --rule:#cfcfcf;
  --footer:#333333;
  --footer-line:#4a4a4a;
  --footer-text:#d8d8d8;
  --white:#fff;
}
*{margin:0;padding:0;box-sizing:border-box}
html,body{width:1200px;height:1170px;overflow:hidden;background:var(--white)}
body{position:relative;font-family:"Oxygen",sans-serif;color:var(--text)}
.abs{position:absolute}

/* header */
.top-border{left:0;top:0;width:1200px;height:4px;background:var(--plum)}
.brand{left:177px;top:50px;display:flex;align-items:center;gap:14px}
.brand-mark{width:30px;height:30px;background:var(--gold)}
.brand-name{font-size:44px;font-weight:400;color:var(--plum);letter-spacing:1px}
.live-chat{left:858px;top:13px;width:164px;height:90px}
.live-chat-box{position:absolute;left:0;top:28px;width:164px;height:62px;background:linear-gradient(#f6cf3a,#e7b400);border:1px solid #c99b00}
.live-chat-title{position:absolute;left:8px;top:34px;font-size:20px;font-weight:700;color:var(--white)}
.live-chat-sub{position:absolute;left:8px;top:69px;font-size:8px;color:#4a3a00}
.live-chat-person{position:absolute;left:102px;top:0;width:60px;height:90px;background:linear-gradient(#c9a27e,#8a5a3a);border-radius:30px 30px 0 0}
.call-us{left:856px;top:110px;font-size:15.5px;color:var(--plum)}
.call-us b{font-weight:700}

/* nav */
.main-nav{left:0;top:134px;width:1200px;height:37px;background:var(--plum)}
.main-nav a{position:absolute;top:11px;font-size:13px;font-weight:700;color:var(--white);text-decoration:none;letter-spacing:.3px}
.main-nav a.current{color:#d99bbb;font-weight:400}
.main-nav i{position:absolute;top:17px;width:3px;height:3px;background:var(--white);border-radius:50%}

/* hero */
.hero{left:0;top:171px;width:1200px;height:300px;background:radial-gradient(ellipse at 45% 50%,#5d86ad 0%,#8fb0cf 40%,#c7d8e7 75%,#a9c0d6 100%)}
.hero-dots{left:175px;top:445px;display:flex;gap:8px}
.hero-dots span{width:10px;height:10px;background:var(--white)}
.hero-dots span:first-child{background:#d6dbe2}
.quick-contact{left:821px;top:190px;width:203px;height:250px;background:var(--gold);border:2px solid #ececec;border-radius:5px 5px 4px 4px;overflow:hidden}
.quick-contact h2{height:33px;background:#333;color:var(--white);font-size:16px;font-weight:700;text-align:center;line-height:34px;letter-spacing:.8px}
.qc-field{position:absolute;left:14px;width:174px;height:23px;background:var(--white);border-radius:2px;font-size:10px;color:#999;padding:6px 7px}
.qc-submit{position:absolute;left:122px;top:216px;width:65px;height:22px;background:#2d2d2d;color:var(--white);font-size:10.5px;font-weight:700;text-align:center;line-height:22px;border-radius:2px}

/* services */
.section-title{font-family:"Oxygen",sans-serif;color:var(--plum);font-size:21px;font-weight:700}
.services-title{left:194px;top:491px}
.view-all{left:948px;top:490px;width:61px;height:22px;background:var(--gold);color:var(--white);font-size:11px;font-weight:700;text-align:center;line-height:22px;border-radius:2px}
.rule{height:1px;background:var(--rule)}
.rule-services{left:160px;top:532px;width:883px;height:2px}
.rule-mid{left:160px;top:782px;width:883px}
.arrow{top:647px;width:22px;height:22px;background:#c8c8c8;display:flex;align-items:center;justify-content:center}
.service-card{top:561px;width:141px;height:198px;background:var(--gold);border-radius:3px;overflow:hidden;text-align:center}
.service-photo{height:129px}
.service-card h3{font-size:10.5px;font-weight:700;color:var(--ink);margin-top:9px}
.service-card p{font-size:9.5px;color:#2a2a2a;line-height:12px;margin-top:1px}
.service-card .more{font-size:9.5px;font-weight:700;color:var(--ink);margin-top:8px;display:block}

/* welcome & news */
.welcome-title{left:175px;top:798px;font-family:"Arimo",sans-serif;font-size:20px;color:#8b0b1e}
.welcome-text{left:175px;top:825px;width:597px;font-size:10.6px;line-height:17px;color:var(--ink)}
.read-more{font-size:10px;font-weight:700;color:var(--ink)}
.news-title{left:793px;top:800px;font-family:"Arimo",sans-serif;font-size:20px;color:#8b0b1e}
.news-item{left:793px;width:220px;display:flex;gap:6px}
.news-date{width:26px;height:28px;border:1px solid #444;border-radius:2px;text-align:center;flex:none;overflow:hidden}
.news-date b{display:block;background:#555;color:var(--white);font-size:10px;height:14px;line-height:14px}
.news-date span{display:block;font-size:8px;font-weight:700;color:#333;line-height:13px}
.news-item p{font-size:10.5px;line-height:12.5px;color:var(--muted)}

/* footer */
.footer{left:0;top:930px;width:1200px;height:209px;background:var(--footer)}
.footer h4{position:absolute;top:20px;font-size:13px;font-weight:400;color:#e8e8e8;letter-spacing:.4px}
.footer-line{position:absolute;left:160px;top:36px;width:883px;height:1px;background:var(--footer-line)}
.quick-links{position:absolute;left:176px;top:55px;list-style:none}
.quick-links li{font-size:10.5px;color:var(--footer-text);height:18.5px;letter-spacing:.2px}
.newsletter-text{position:absolute;left:305px;top:55px;width:195px;font-size:11.5px;line-height:16px;color:var(--footer-text);letter-spacing:.3px}
.newsletter-input{position:absolute;left:303px;top:140px;width:156px;height:22px;background:var(--white);border-radius:2px;font-size:11px;color:#999;padding:4px 5px}
.newsletter-submit{position:absolute;left:303px;top:173px;width:71px;height:22px;background:var(--plum);color:var(--white);font-size:12.5px;font-weight:700;text-align:center;line-height:22px}
.contact-text{position:absolute;left:539px;top:56px;width:290px;font-size:11.5px;line-height:14.5px;color:var(--footer-text);letter-spacing:.3px}
.contact-map{position:absolute;left:539px;top:92px;width:113px;height:89px;border:2px solid #eee;background:linear-gradient(135deg,#e9e6de,#d7dccf)}
.contact-row{position:absolute;left:666px;display:flex;gap:14px;font-size:11px;line-height:14px;color:var(--footer-text)}
.contact-row svg{flex:none}
.footer-brand{position:absolute;left:841px;top:108px;display:flex;align-items:center;gap:10px}
.footer-brand .brand-mark{width:22px;height:22px}
.footer-brand span{font-size:34px;color:var(--plum)}
.copyright{left:0;top:1139px;width:1200px;height:31px;background:var(--footer);border-top:1px solid var(--footer-line);text-align:center;font-size:9.5px;line-height:30px;color:#e6e6e6}
</style>
</head>
<body>

<div class="abs top-border"></div>

<header>
  <div class="abs brand"><span class="brand-mark"></span><span class="brand-name">plumbwick</span></div>
  <div class="abs live-chat">
    <div class="live-chat-box"></div>
    <div class="live-chat-title">Live Chat</div>
    <div class="live-chat-sub">Click to chat with us now!</div>
    <div class="live-chat-person" role="img" aria-label="Photo of a support agent wearing a headset"></div>
  </div>
  <div class="abs call-us">CALL US: <b>020 7946 0182</b></div>
</header>

<nav class="abs main-nav">
  <a class="current" style="left:176px">HOME</a><i style="left:237px"></i>
  <a style="left:267px">ABOUT US</a><i style="left:351px"></i>
  <a style="left:374px">WHAT WE DO</a><i style="left:480px"></i>
  <a style="left:503px">NEWS BLOG</a><i style="left:603px"></i>
  <a style="left:626px">ARTICLES</a><i style="left:710px"></i>
  <a style="left:733px">CLIENTS</a><i style="left:804px"></i>
  <a style="left:831px">PARTNERS</a><i style="left:921px"></i>
  <a style="left:945px">CONTACT US</a>
</nav>

<section class="abs hero" role="img" aria-label="Close-up photo of a hand holding a blue jigsaw puzzle piece over a puzzle"></section>
<div class="abs hero-dots"><span></span><span></span><span></span></div>

<form class="abs quick-contact">
  <h2>QUICK CONTACT</h2>
  <div class="qc-field" style="top:45px">Name</div>
  <div class="qc-field" style="top:74px">Email</div>
  <div class="qc-field" style="top:103px">Phone</div>
  <div class="qc-field" style="top:131px;height:79px">Message</div>
  <div class="qc-submit">SUBMIT</div>
</form>

<section>
  <h2 class="abs section-title services-title">Our Services</h2>
  <div class="abs view-all">VIEW ALL</div>
  <div class="abs rule rule-services"></div>

  <div class="abs arrow" style="left:160px"><svg width="8" height="12" viewBox="0 0 8 12"><path d="M7 1 2 6l5 5" stroke="#555" stroke-width="2" fill="none"/></svg></div>
  <div class="abs arrow" style="left:1021px"><svg width="8" height="12" viewBox="0 0 8 12"><path d="M1 1l5 5-5 5" stroke="#555" stroke-width="2" fill="none"/></svg></div>

  <article class="abs service-card" style="left:195px">
    <div class="service-photo" role="img" aria-label="Photo of a business team joining hands in a circle" style="background:linear-gradient(160deg,#f2f2f2,#8d8d8d 60%,#3a3a3a)"></div>
    <h3>IT Support &amp; Management</h3><p>Lorem ipsum djnsdolor sit<br>amet, consectetuer</p><span class="more">READ MORE</span>
  </article>
  <article class="abs service-card" style="left:362px">
    <div class="service-photo" role="img" aria-label="Illustration of a glowing cloud connected to devices" style="background:radial-gradient(circle at 50% 45%,#5fd0f5,#0a6fa8 45%,#04233f)"></div>
    <h3>Cloud Computing</h3><p>Lorem ipsum djnsdolor sit<br>amet, consectetuer</p><span class="more">READ MORE</span>
  </article>
  <article class="abs service-card" style="left:530px">
    <div class="service-photo" role="img" aria-label="Photo of a stressed worker at a computer in front of a falling chart" style="background:linear-gradient(160deg,#dbe8f2,#9fbfd8 55%,#eef3f7)"></div>
    <h3>Disaster Recovery</h3><p>Lorem ipsum djnsdolor sit<br>amet, consectetuer</p><span class="more">READ MORE</span>
  </article>
  <article class="abs service-card" style="left:697px">
    <div class="service-photo" role="img" aria-label="Photo of a hand touching a glowing server rack" style="background:linear-gradient(160deg,#3d6d9e,#1a3e66 50%,#c07a86)"></div>
    <h3>Virtualisation</h3><p>Lorem ipsum djnsdolor sit<br>amet, consectetuer</p><span class="more">READ MORE</span>
  </article>
  <article class="abs service-card" style="left:864px">
    <div class="service-photo" role="img" aria-label="Photo of a businessman facing a wall of sketched diagrams" style="background:linear-gradient(170deg,#4a4a4a,#a9a9a9 55%,#d6d6d6)"></div>
    <h3>CAD Services</h3><p>Lorem ipsum djnsdolor sit<br>amet, consectetuer</p><span class="more">READ MORE</span>
  </article>

  <div class="abs rule rule-mid"></div>
</section>

<section>
  <h2 class="abs welcome-title">Welcome to Plumbwick</h2>
  <p class="abs welcome-text">Lorem ipsum dolor sit amet, consectetuer adipiscing elit, sed diam nonummy nibh euismod tincidunt ut laoreet dolore mag na aliquam erat volutpat. Ut wisi enim ad minim veniam, quis nostrud exerci tation ullamcorper suscipit lobortis nisl ut ali quip ex ea commodo consequat. Duis autem vel eum iriure dolor in hendrerit in vulputate velit esse molestie consequat, vel illum dolore eu feugiat nulla facilisis at vero eros et accumsan et iusto odio dignissim qui blandit.</p>
  <span class="abs read-more" style="left:706px;top:898px">READ MORE</span>
</section>

<aside>
  <h2 class="abs news-title">News</h2>
  <div class="abs news-item" style="top:830px">
    <div class="news-date"><b>17</b><span>APR</span></div>
    <p>Excepteur sint occaecat cooid ent, su ntin culpa qui officia deserunt.</p>
  </div>
  <div class="abs news-item" style="top:867px">
    <div class="news-date"><b>16</b><span>APR</span></div>
    <p>Excepteur sint occaecat cooid ent, su ntin culpa qui officia deserunt.</p>
  </div>
  <span class="abs read-more" style="left:947px;top:898px">READ MORE</span>
</aside>

<footer class="abs footer">
  <h4 style="left:177px">QUICK LINKS</h4>
  <h4 style="left:302px">NEWS LETTER</h4>
  <h4 style="left:537px">CONTACT INFO</h4>
  <div class="footer-line"></div>

  <ul class="quick-links">
    <li>HOME</li><li>ABOUT US</li><li>WHAT WE DO</li><li>NEWS BLOG</li>
    <li>ARTICLES</li><li>CLIENTS</li><li>PARTNERS</li><li>CONTACT US</li>
  </ul>

  <p class="newsletter-text">Lorem ipsum minim veniam, quis nostrud exerci tation ullamcorper suscipit. Duis autem vel eum iriure dolor in hendrerit in vulputate velit esse mole.</p>
  <div class="newsletter-input">Enter your email address</div>
  <div class="newsletter-submit">SUBMIT</div>

  <p class="contact-text">Lorem ipsum minim veniam, quis nostrud exerci tation ullamcorper suscipit.</p>
  <div class="contact-map" role="img" aria-label="Street map showing the office location"></div>

  <div class="contact-row" style="top:92px">
    <svg width="12" height="16" viewBox="0 0 12 16"><path d="M6 1a5 5 0 0 0-5 5c0 4 5 9 5 9s5-5 5-9a5 5 0 0 0-5-5z" fill="#ccc"/><circle cx="6" cy="6" r="2" fill="#333"/></svg>
    <span>Larch House<br>48-52 Fenwick Lane<br>London EC2A 7QT<br>United Kingdom</span>
  </div>
  <div class="contact-row" style="top:163px">
    <svg width="14" height="14" viewBox="0 0 14 14"><circle cx="7" cy="7" r="6" stroke="#ccc" stroke-width="1.3" fill="none"/><path d="M5 4c-1 1 0 4 2 5.5s3 1 3.5 0L9 8l-1 .7C7 8 6 7 5.5 6l.6-1z" fill="#ccc"/></svg>
    <span>020 7946 0182</span>
  </div>
  <div class="contact-row" style="top:182px">
    <svg width="14" height="12" viewBox="0 0 14 12"><rect x="1" y="2" width="12" height="8" fill="none" stroke="#ccc" stroke-width="1.3"/><path d="M1 2l6 5 6-5" stroke="#ccc" stroke-width="1.3" fill="none"/></svg>
    <span>hello@plumbwick.net</span>
  </div>

  <div class="footer-brand"><span class="brand-mark"></span><span>plumbwick</span></div>
</footer>

<div class="abs copyright">COPYRIGHT 2014 | &nbsp;PLUMBWICK | ALL RIGHTS RSERVED.</div>

</body>
</html>
```